Corvane Card

The logo is the Spanish flag colors I want a vibrant eye catching design with the yellow / red colors over either Navy or white background or black even ,
Would like a 2D feel to the logo with another lighter color logo under it look ,

Contact Information for Business Card

Corvane Flooring
Teodor Vashkin
Main Number
Cell Number
Fax Number

Website on the side of the card somewhere

Font styles to use
Sans Serif

Colors
ec1f27
ffc214

Requirements
Must have
• 2 logos feel one is bolder and the other one underneath very light

```html
<!DOCTYPE html>
<html lang="en">
<head>
<meta charset="utf-8">
<title>Corvane Flooring – Business Card</title>
<link href="https://fonts.googleapis.com/css2?family=Orbitron:wght@800&family=Arimo:wght@400;700&display=swap" rel="stylesheet">
<style>
  :root {
    --scene: #2b2b2d;
    --card: #221f20;
    --ghost: #2c292a;
    --red: #ec1f27;
    --yellow: #ffc214;
    --white: #f4f4f4;
    --rule: #5a5658;
  }
  * { box-sizing: border-box; margin: 0; padding: 0; }
  html, body { width: 1200px; height: 866px; overflow: hidden; }
  body {
    background: var(--scene);
    display: flex; align-items: center; justify-content: center; gap: 40px;
    font-family: "Arimo", Arial, sans-serif;
  }
  .card {
    position: relative;
    width: 540px; height: 309px;
    background: var(--card);
    box-shadow: 0 14px 30px rgba(0,0,0,.45);
    overflow: hidden;
  }

  /* faint second logo layer behind the content */
  .ghost-logo {
    position: absolute; left: 50%; top: 8px; transform: translateX(-50%);
    font-family: "Orbitron", sans-serif; font-weight: 800;
    font-size: 78px; letter-spacing: .02em; line-height: 1;
    color: var(--ghost); white-space: nowrap; text-transform: uppercase;
    user-select: none;
  }
  .front .ghost-logo { top: auto; bottom: 10px; font-size: 82px; }

  .brand { display: flex; align-items: center; gap: 10px; position: relative; }
  .brand-mark { width: 22px; height: 22px; background: var(--yellow); flex: none; }
  .brand-name {
    font-family: "Orbitron", sans-serif; font-weight: 800;
    color: var(--red); line-height: 1.2; letter-spacing: .1em;
    text-transform: uppercase;
  }

  /* contact side */
  .contact .holder {
    position: absolute; left: 28px; top: 34px;
    font-family: "Orbitron", sans-serif; font-weight: 800;
    font-size: 16px; color: var(--red); letter-spacing: .08em;
    text-transform: uppercase; transform: skewX(-10deg); transform-origin: left bottom;
  }
  .contact .holder-rule {
    position: absolute; left: 28px; top: 64px; width: 300px; height: 1px;
    background: var(--rule);
  }
  .contact .brand { position: absolute; right: 28px; top: 26px; }
  .contact .brand-name { font-size: 14px; }
  .phones { position: absolute; left: 28px; top: 82px; list-style: none; }
  .phones li {
    display: flex; align-items: center; gap: 8px;
    color: var(--white); font-size: 13px; font-weight: 700; line-height: 19px; letter-spacing: .04em;
  }
  .icon { width: 11px; height: 11px; fill: var(--red); flex: none; }
  .online-rule {
    position: absolute; left: 200px; right: 28px; top: 224px; height: 1px;
    background: var(--rule);
  }
  .online { position: absolute; right: 28px; top: 238px; list-style: none; }
  .online li {
    display: flex; align-items: center; justify-content: flex-end; gap: 8px;
    font-size: 13px; line-height: 19px; letter-spacing: .04em;
  }
  .online .email { color: var(--white); }
  .online .web { color: var(--yellow); }

  /* logo side */
  .front .brand { position: absolute; left: 50%; top: 44%; transform: translate(-50%, -50%); gap: 14px; }
  .front .brand-mark { width: 38px; height: 38px; }
  .front .brand-name { font-size: 26px; }
  .front .web {
    position: absolute; left: 0; right: 0; top: 222px; text-align: center;
    color: var(--red); font-size: 13px; letter-spacing: .14em;
  }
</style>
</head>
<body>

  <section class="card contact">
    <span class="ghost-logo" aria-hidden="true">Corvane</span>
    <p class="holder">Teodor Vashkin</p>
    <div class="holder-rule"></div>
    <div class="brand">
      <span class="brand-mark"></span>
      <span class="brand-name">Corvane<br>Flooring</span>
    </div>
    <ul class="phones">
      <li><svg class="icon" viewBox="0 0 12 12"><path d="M1 4c0-2 2-3 5-3s5 1 5 3v1H8V4H4v1H1zM3 6h6l1 5H2z"/></svg>410 620 7731</li>
      <li><svg class="icon" viewBox="0 0 12 12"><path d="M3 0h6v12H3zM4 1.5v8h4v-8z"/></svg>410 620 7745</li>
      <li><svg class="icon" viewBox="0 0 12 12"><path d="M3 0h6v4H3zM0 4h12v6H9v2H3v-2H0zM4 8v3h4V8z"/></svg>410 620 7790</li>
    </ul>
    <div class="online-rule"></div>
    <ul class="online">
      <li class="email">hello@corvanefloors.com<svg class="icon" viewBox="0 0 12 12"><path d="M0 2h12v8H0zM1 3l5 4 5-4z"/></svg></li>
      <li class="web">www.corvanefloors.com<svg class="icon" viewBox="0 0 12 12"><circle cx="6" cy="6" r="5.5"/></svg></li>
    </ul>
  </section>

  <section class="card front">
    <span class="ghost-logo" aria-hidden="true">Corvane</span>
    <div class="brand">
      <span class="brand-mark"></span>
      <span class="brand-name">Corvane<br>Flooring</span>
    </div>
    <p class="web">www.corvanefloors.com</p>
  </section>

</body>
</html>
```